New Year's card HTML

can you produce a best new years wishes 2018 design in HTML for our website as what I would like to send by email towards my network of candidates / customers ...

It must be wow, inspiring , design, meaningfull... MMM those people care about me, or those people will help me to go the extra mile, to help me to achieve my career goals, Your best move, enhance my possibilities, bring the love back

Target Market(s)

CEo's / CMO's/ HRDirectors network of 450k

Coding

Coded - Design and coding required

Number of Pages Required

1 page

Colors

Designer to choose colors to be used in the design.

Requirements
Must have
• Logo / visual / website adress www.moravintel.com and a call to action
Should not have
• no sound as our business is confidential

```html
<!DOCTYPE html>
<html lang="en">
<head>
<meta charset="utf-8">
<title>Moravintel – Happy New Year 2018</title>
<link rel="stylesheet" href="https://fonts.googleapis.com/css2?family=Anton&family=Cinzel:wght@400&family=Oswald:wght@600&display=swap">
<style>
  :root {
    --night: #0a0d16;
    --indigo: #1c1a4a;
    --plum: #241233;
    --glow: #e8a36a;
    --white: #ffffff;
    --gold: #f9c513;
    --coral: #ff5b3c;
    --green: #3cb43c;
    --crimson: #e41b45;
  }
  html, body {
    margin: 0;
    padding: 0;
    overflow: hidden;
    background: var(--night);
  }
  .card {
    position: relative;
    width: 1200px;
    height: 1040px;
    overflow: hidden;
    background: var(--night);
  }
  .fireworks-backdrop {
    position: absolute;
    inset: 0;
    background:
      radial-gradient(circle at 9% 47%, rgba(232,163,106,.55) 0, rgba(232,163,106,0) 14%),
      radial-gradient(circle at 32% 68%, rgba(232,163,106,.55) 0, rgba(232,163,106,0) 14%),
      radial-gradient(circle at 79% 57%, rgba(232,163,106,.45) 0, rgba(232,163,106,0) 14%),
      radial-gradient(circle at 95% 51%, rgba(232,163,106,.45) 0, rgba(232,163,106,0) 12%),
      radial-gradient(circle at 30% 42%, rgba(80,140,160,.35) 0, rgba(80,140,160,0) 16%),
      radial-gradient(ellipse at 50% 58%, var(--indigo) 0, rgba(28,26,74,0) 60%),
      linear-gradient(180deg, var(--night) 0%, var(--night) 22%, var(--indigo) 52%, var(--plum) 100%);
  }
  .brand-name {
    position: absolute;
    left: 0;
    top: 198px;
    width: 1200px;
    margin: 0;
    text-align: center;
    font-family: "Cinzel", serif;
    font-weight: 400;
    font-size: 48px;
    letter-spacing: 5px;
    color: var(--white);
    line-height: 1;
  }
  .greeting {
    position: absolute;
    left: 0;
    top: 0;
    width: 1200px;
    height: 1040px;
  }
  .greeting .rule line { stroke: var(--white); stroke-width: 3; }
  .greeting .rule circle { fill: var(--gold); stroke: var(--white); stroke-width: 2; }
  .headline {
    font-family: "Anton", sans-serif;
    fill: var(--white);
  }
  .year {
    font-family: "Anton", sans-serif;
    stroke: var(--white);
    stroke-width: 10;
    stroke-linejoin: round;
    paint-order: stroke fill;
  }
  .year .d1 { fill: var(--gold); }
  .year .d2 { fill: var(--coral); }
  .year .d3 { fill: var(--green); }
  .year .d4 { fill: var(--crimson); }
  .cta {
    position: absolute;
    left: 478px;
    top: 914px;
    width: 244px;
    height: 58px;
    border-radius: 29px;
    background: var(--gold);
    color: var(--white);
    font-family: "Oswald", sans-serif;
    font-weight: 600;
    font-size: 29px;
    line-height: 58px;
    text-align: center;
    text-decoration: none;
    letter-spacing: -0.5px;
  }
</style>
</head>
<body>
<main class="card">
  <div class="fireworks-backdrop" role="img" aria-label="Night sky filled with golden fireworks bursts and soft coloured bokeh lights"></div>

  <h1 class="brand-name">MORAVINTEL</h1>

  <svg class="greeting" viewBox="0 0 1200 1040" aria-label="Happy New Year 2018">
    <g class="rule">
      <line x1="386" y1="289" x2="816" y2="289" stroke-dasharray="60 32"/>
      <circle cx="464" cy="289" r="6"/>
      <circle cx="556" cy="289" r="6"/>
      <circle cx="648" cy="289" r="6"/>
      <circle cx="741" cy="289" r="6"/>
    </g>

    <text class="headline" x="386" y="464" font-size="176" textLength="428" lengthAdjust="spacingAndGlyphs">HAPPY</text>
    <text class="headline" x="386" y="586" font-size="118" textLength="426" lengthAdjust="spacingAndGlyphs">NEW YEAR</text>

    <g class="rule">
      <line x1="386" y1="610" x2="816" y2="610" stroke-dasharray="60 32"/>
      <circle cx="464" cy="610" r="6"/>
      <circle cx="556" cy="610" r="6"/>
      <circle cx="648" cy="610" r="6"/>
      <circle cx="741" cy="610" r="6"/>
    </g>

    <text class="year" x="393" y="846" font-size="240" textLength="416" lengthAdjust="spacingAndGlyphs"><tspan class="d1">2</tspan><tspan class="d2">0</tspan><tspan class="d3">1</tspan><tspan class="d4">8</tspan></text>
  </svg>

  <a class="cta" href="https://www.moravintel.com">VISIT OUR SITE</a>
</main>
</body>
</html>
```